Redesign of business card for Cedar Ridge Mechanical

We are looking for a new design for our business cards for Cedar Ridge Mechanical. We are a plumbing & HVAC construction company, operating on the West Coast of Canada and USA. Logo attached.
Industry/Entity Type
Construction - Plumbing & HVAC
Contact Information for Business Card
Name, address, phone numbers, email, website address
Look and feel
Each slider illustrates characteristics of the customer's brand and the style your logo design should communicate.

```html
<!DOCTYPE html>
<html lang="en">
<head>
<meta charset="utf-8">
<title>Cedar Ridge Mechanical – Business Card</title>
<link href="https://fonts.googleapis.com/css2?family=Poppins:wght@300;400;600;700&display=swap" rel="stylesheet">
<style>
  :root {
    --backdrop: #232324;
    --card: #1f1f21;
    --band: #19191b;
    --rule: #2e2e31;
    --ink: #ffffff;
    --ink-soft: #e6e6e6;
  }
  * { box-sizing: border-box; margin: 0; padding: 0; }
  html, body { width: 1200px; height: 711px; overflow: hidden; }
  body {
    background: var(--backdrop);
    font-family: "Poppins", sans-serif;
    color: var(--ink);
    position: relative;
  }
  .card {
    position: absolute;
    top: 200px;
    width: 540px;
    height: 310px;
    background: var(--card);
    border-radius: 4px;
    box-shadow: 0 14px 30px rgba(0,0,0,.55);
    overflow: hidden;
  }
  .card--front { left: 40px; }
  .card--back { left: 620px; }

  .band {
    position: absolute;
    left: 0; right: 0;
    background: var(--band);
    border-top: 1px solid var(--rule);
    border-bottom: 1px solid var(--rule);
  }

  .wordmark {
    display: flex;
    align-items: center;
    gap: 12px;
    font-weight: 600;
    color: var(--ink);
    letter-spacing: .5px;
    text-transform: uppercase;
  }
  .wordmark__square {
    width: 30px; height: 30px;
    border: 4px solid var(--ink);
    border-radius: 4px;
    flex: none;
  }

  /* front */
  .card--front .wordmark {
    position: absolute;
    left: 0; right: 0; top: 100px;
    justify-content: center;
    font-size: 24px;
  }
  .card--front .site {
    position: absolute;
    left: 0; right: 0; top: 212px;
    text-align: center;
    font-size: 13px;
    font-weight: 400;
    letter-spacing: .6px;
    color: var(--ink-soft);
  }
  .card--front .band { top: 244px; height: 36px; }

  /* back */
  .card--back .wordmark {
    position: absolute;
    left: 34px; top: 60px;
    font-size: 17px;
    width: 230px;
    line-height: 1.25;
  }
  .person {
    position: absolute;
    right: 30px; top: 50px;
    text-align: right;
  }
  .person__name { font-size: 26px; line-height: 1.1; }
  .person__first { font-weight: 700; }
  .person__last { font-weight: 300; }
  .person__role { font-size: 12px; font-weight: 400; margin-top: 2px; }

  .card--back .band--contact { top: 120px; height: 100px; border-bottom: none; background: linear-gradient(var(--band), var(--card)); }
  .contact {
    position: absolute;
    right: 30px; top: 132px;
    list-style: none;
    text-align: right;
    font-size: 13px;
    font-weight: 300;
    line-height: 22px;
  }
  .contact li { display: flex; align-items: center; justify-content: flex-end; gap: 10px; }
  .contact svg { width: 13px; height: 13px; fill: none; stroke: var(--ink); stroke-width: 1.6; }

  .card--back .band--address { top: 236px; height: 52px; }
  .address {
    position: absolute;
    left: 30px; top: 241px;
    display: flex;
    gap: 10px;
    align-items: center;
    font-size: 13px;
    font-weight: 400;
    line-height: 20px;
  }
  .address svg { width: 14px; height: 18px; fill: none; stroke: var(--ink); stroke-width: 1.6; }
</style>
</head>
<body>

  <section class="card card--front" aria-label="Card front">
    <div class="wordmark"><span class="wordmark__square"></span>Cedar Ridge Mechanical</div>
    <p class="site">www.website.com</p>
    <div class="band"></div>
  </section>

  <section class="card card--back" aria-label="Card back">
    <div class="wordmark"><span class="wordmark__square"></span>Cedar Ridge Mechanical</div>

    <div class="person">
      <p class="person__name"><span class="person__first">Marta</span> <span class="person__last">Lindqvist</span></p>
      <p class="person__role">Founder &amp; CEO</p>
    </div>

    <div class="band band--contact"></div>
    <ul class="contact">
      <li>(604) 555-0148
        <svg viewBox="0 0 16 16"><path d="M4 1.5l2.2 3-1.4 1.6c.8 1.9 2.3 3.4 4.2 4.2l1.6-1.4 3 2.2-1 2.6C7.5 13.5 2.5 8.5 1.4 2.5z"/></svg>
      </li>
      <li>www.yourwebsite.com
        <svg viewBox="0 0 16 16"><circle cx="8" cy="8" r="6.5"/><path d="M1.5 8h13M8 1.5c2.2 2 2.2 11 0 13M8 1.5c-2.2 2-2.2 11 0 13"/></svg>
      </li>
      <li>info@yourwebsite.com
        <svg viewBox="0 0 16 16"><rect x="1.5" y="3.5" width="13" height="9" rx="1"/><path d="M1.5 4l6.5 5 6.5-5"/></svg>
      </li>
    </ul>

    <div class="band band--address"></div>
    <div class="address">
      <svg viewBox="0 0 14 18"><path d="M7 16.5S1.5 10.5 1.5 6.5a5.5 5.5 0 0 1 11 0c0 4-5.5 10-5.5 10z"/><circle cx="7" cy="6.5" r="2"/></svg>
      <p>1840 Harbour Way Suite 300<br>Vancouver, BC V6B 1A1</p>
    </div>
  </section>

</body>
</html>
```